Tech business card design

We need an amazing business card design for our new business 'Pexla' a marketing tech startup based in Sydney, Australia. We provide an online marketplace for businesses to search and buy advertising media, connect with service providers and learn more about marketing. We wish to communicate 'cool tech', reliability and professionalism and design based around our logo.

Target Market(s)

Business Owners

Contact Information for Business Card

Name
Position
Email Address
Website
Phone Number

Font styles to use
Other font styles liked:
• Avenir & Avenir Next

Colors

Designer to choose colors to be used in the design.

```html
<!DOCTYPE html>
<html lang="en">
<head>
<meta charset="utf-8">
<title>Pexla Business Card</title>
<link rel="stylesheet" href="https://fonts.googleapis.com/css2?family=Mulish:wght@400;800;900&display=swap">
<style>
  :root {
    --navy: #16163f;
    --ink: #1b1b45;
    --paper: #ffffff;
    --backdrop-light: #dcdcdc;
    --backdrop-dark: #a9a9a9;
  }
  * { box-sizing: border-box; margin: 0; padding: 0; }
  html, body {
    width: 1200px;
    height: 900px;
    overflow: hidden;
  }
  body {
    background: radial-gradient(ellipse at 50% 45%, var(--backdrop-light) 0%, var(--backdrop-dark) 100%);
    font-family: "Mulish", sans-serif;
    color: var(--ink);
  }
  .card-row {
    position: absolute;
    inset: 0;
    display: flex;
    justify-content: center;
    align-items: center;
    gap: 70px;
  }
  .card {
    position: relative;
    width: 340px;
    height: 540px;
    background: var(--paper);
    border: 11px solid var(--navy);
    border-radius: 30px;
    box-shadow: 0 14px 30px rgba(0,0,0,0.25);
  }
  .wordmark {
    position: absolute;
    top: 26px;
    left: 22px;
    font-weight: 900;
    font-size: 92px;
    line-height: 1;
    letter-spacing: -2px;
    color: var(--navy);
  }
  .identity {
    position: absolute;
    top: 228px;
    left: 0;
    right: 0;
    text-align: center;
  }
  .person-name {
    font-weight: 900;
    font-size: 24px;
    line-height: 1.1;
    color: var(--navy);
  }
  .person-role {
    font-weight: 400;
    font-size: 20px;
    line-height: 1.2;
  }
  .divider {
    width: 26px;
    height: 2px;
    background: var(--ink);
    margin: 26px auto 0;
  }
  .contact-icons {
    position: absolute;
    top: 370px;
    left: 0;
    right: 0;
    display: flex;
    justify-content: center;
    gap: 30px;
  }
  .contact-icons svg { width: 18px; height: 18px; }
  .contact-lines {
    position: absolute;
    top: 404px;
    left: 0;
    right: 0;
    text-align: center;
    font-size: 19px;
    line-height: 1.22;
    font-weight: 400;
  }
  .back-site {
    position: absolute;
    right: 24px;
    bottom: 24px;
    font-size: 20px;
    font-weight: 400;
  }
</style>
</head>
<body>
  <main class="card-row">
    <section class="card card-front">
      <div class="wordmark">Pexla</div>
      <div class="identity">
        <p class="person-name">Daniel Rowe</p>
        <p class="person-role">Founder, Director</p>
        <div class="divider"></div>
      </div>
      <div class="contact-icons">
        <svg viewBox="0 0 24 24" aria-label="Phone">
          <circle cx="12" cy="12" r="11" fill="var(--navy)"/>
          <path d="M8.5 6.5c.6-.4 1.2-.3 1.5.3l1 2c.2.5.1 1-.3 1.3l-.8.6c.6 1.3 1.6 2.3 2.9 2.9l.6-.8c.3-.4.8-.5 1.3-.3l2 1c.6.3.7.9.3 1.5l-.7 1c-.5.6-1.3.8-2 .5-3.3-1.3-5.8-3.8-7.1-7.1-.3-.7-.1-1.5.5-2z" fill="#fff"/>
        </svg>
        <svg viewBox="0 0 24 24" aria-label="Email">
          <rect x="2" y="5" width="20" height="14" rx="1.5" fill="var(--navy)"/>
          <path d="M3 6.5l9 6.5 9-6.5" fill="none" stroke="#fff" stroke-width="1.4"/>
        </svg>
        <svg viewBox="0 0 24 24" aria-label="Website">
          <circle cx="12" cy="12" r="10" fill="none" stroke="var(--navy)" stroke-width="2"/>
          <ellipse cx="12" cy="12" rx="4.5" ry="10" fill="none" stroke="var(--navy)" stroke-width="1.6"/>
          <path d="M2 12h20M4 7h16M4 17h16" stroke="var(--navy)" stroke-width="1.4"/>
        </svg>
      </div>
      <div class="contact-lines">
        <p>+61 (0)400 555 018</p>
        <p>daniel@pexlamedia.com.au</p>
        <p>www.pexlamedia.com.au</p>
      </div>
    </section>

    <section class="card card-back">
      <div class="wordmark">Pexla</div>
      <p class="back-site">www.pexlamedia.com.au</p>
    </section>
  </main>
</body>
</html>
```